QVR business card

Need a business card for a company that provides instructional design and elearning development services. The website is here: http://quorvane.studio/

I'm attaching a current logo, as well as the old business card design. While I like to keep it clean, the old design is too simplistic for my liking. The only idea I want to reuse from the old design is placing industry jargon on the back of the card, just need a better way to present it. But if you have other ideas for the back--feel free to experiment.

Please use the colors complementary to the color we have on the website. Thank you!

```html
<!DOCTYPE html>
<html lang="en">
<head>
<meta charset="utf-8">
<title>QVR Business Card</title>
<link rel="stylesheet" href="https://fonts.googleapis.com/css2?family=Open+Sans:wght@400;600;700;800&family=PT+Sans+Narrow&display=swap">
<style>
  :root {
    --backdrop: #1f1f21;
    --teal: #22b5b0;
    --teal-dark: #1a9f9a;
    --gold: #d8c98a;
    --ink: #2b2b2b;
    --paper: #ffffff;
  }
  * { margin: 0; padding: 0; box-sizing: border-box; }
  html, body { width: 1200px; height: 781px; overflow: hidden; background: var(--backdrop); }
  .canvas { position: relative; width: 1200px; height: 781px; }

  .card { position: absolute; width: 520px; height: 297px; top: 242px; overflow: hidden; }

  /* Back */
  .card-back { left: 50px; background: var(--teal); color: var(--paper); }
  .headline {
    position: absolute; left: 28px; top: 26px;
    font-family: "Open Sans", sans-serif; font-weight: 800;
    line-height: 0.95; text-transform: uppercase;
  }
  .headline span { display: block; font-size: 50px; }
  .headline .headline-big { font-size: 72px; line-height: 0.9; }
  .divider { position: absolute; left: 218px; top: 32px; width: 1px; height: 232px; background: rgba(255,255,255,0.75); }
  .services {
    position: absolute; left: 234px; top: 34px; list-style: none;
    font-family: "PT Sans Narrow", sans-serif; font-size: 27px; line-height: 38px;
    text-transform: uppercase; letter-spacing: 0.3px;
  }

  /* Front */
  .card-front { left: 630px; background: var(--paper); }
  .holder { position: absolute; left: 30px; top: 34px; font-family: "Open Sans", sans-serif; }
  .holder-name { color: var(--teal); font-weight: 700; font-size: 15px; letter-spacing: 0.5px; }
  .holder-role { color: var(--ink); font-size: 11px; margin-top: 2px; }
  .rule { position: absolute; left: 0; top: 0; }
  .brand {
    position: absolute; right: 36px; top: 104px; display: flex; align-items: center; gap: 10px;
    font-family: "Open Sans", sans-serif; font-weight: 700; font-size: 40px; color: var(--teal); letter-spacing: 2px;
  }
  .brand-dot { width: 16px; height: 16px; border-radius: 50%; background: var(--gold); }
  .contact {
    position: absolute; right: 30px; bottom: 46px; list-style: none; text-align: right;
    font-family: "Open Sans", sans-serif; font-size: 11px; color: var(--ink); line-height: 22px;
  }
  .contact li { display: flex; justify-content: flex-end; align-items: center; gap: 8px; }
  .contact svg { width: 13px; height: 13px; }
  .website {
    position: absolute; left: 0; bottom: 0; width: 220px; height: 24px; background: var(--teal);
    border-top-right-radius: 12px;
    font-family: "Open Sans", sans-serif; font-size: 10px; color: var(--paper); letter-spacing: 1px;
    padding: 5px 0 0 24px;
  }
  .base-line { position: absolute; left: 220px; right: 0; bottom: 4px; height: 2px; background: var(--gold); }
</style>
</head>
<body>
<div class="canvas">

  <section class="card card-back">
    <h2 class="headline">
      <span>How</span>
      <span>Can</span>
      <span class="headline-big">We</span>
      <span>Help?</span>
    </h2>
    <div class="divider"></div>
    <ul class="services">
      <li>Mobile Learning SCORM</li>
      <li>Instructional Design LMS</li>
      <li>MOOCs eLearning HTML5</li>
      <li>Adult Learning Theory</li>
      <li>Gamification Classroom</li>
      <li>xAPI Blended Learning</li>
    </ul>
  </section>

  <section class="card card-front">
    <svg class="rule" width="520" height="297" viewBox="0 0 520 297" aria-hidden="true">
      <line x1="30" y1="76" x2="200" y2="76" stroke="var(--teal)" stroke-width="3"/>
      <line x1="200" y1="76" x2="470" y2="76" stroke="var(--gold)" stroke-width="1.5"/>
      <circle cx="472" cy="76" r="3" fill="var(--gold)"/>
    </svg>
    <div class="holder">
      <div class="holder-name">MAREK VENHOLLOW</div>
      <div class="holder-role">Managing Director</div>
    </div>
    <div class="brand"><span class="brand-dot"></span>QVR</div>
    <ul class="contact">
      <li>212-555-0187
        <svg viewBox="0 0 16 16" aria-hidden="true"><circle cx="8" cy="8" r="8" fill="var(--teal)"/><path d="M5 4.5l1.6-.3 1 2.2-1 .8a5 5 0 0 0 2.2 2.2l.8-1 2.2 1-.3 1.6C9 11.5 4.5 7 5 4.5z" fill="#fff"/></svg>
      </li>
      <li>mvenhollow@quorvane.studio
        <svg viewBox="0 0 16 16" aria-hidden="true"><circle cx="8" cy="8" r="8" fill="var(--teal)"/><rect x="4" y="5.5" width="8" height="5.5" fill="none" stroke="#fff" stroke-width="1"/><path d="M4 5.5l4 3 4-3" fill="none" stroke="#fff" stroke-width="1"/></svg>
      </li>
    </ul>
    <div class="website">www.quorvane.studio</div>
    <div class="base-line"></div>
  </section>

</div>
</body>
</html>
```